professional business card design for technology company

We are a small technology consulting firm, specialising in consulting based around Cloud and Managed services. Our colour scheme is yellow, blue and white, as you can see in the logos. Although we are based in melbourne australia, due to the nature of our work, our clients can be located anywhere. We are looking for a clean, professional, positive look - similar to our company logo

Target Market(s)

small business

Industry/Entity Type

Business

Contact Information for Business Card

eye catching, designed to incorporate some level of raised printing. Must contain website address, phone number, name and job title

Requirements
Must have
• Logo (attached) - use of the same colour scheme

```html
<!DOCTYPE html>
<html lang="en">
<head>
<meta charset="utf-8">
<title>Nimbora – Business Card</title>
<link rel="stylesheet" href="https://fonts.googleapis.com/css2?family=Exo+2:wght@400;500;600&display=swap">
<style>
  :root {
    --stage: #e9e9e7;
    --card-white: #f7f7f7;
    --card-grey: #5b5b5d;
    --accent-yellow: #f7d51d;
    --accent-blue: #3aa3dd;
    --ink-grey: #555657;
    --ink-white: #ffffff;
    --ghost: #dedede;
  }
  * { box-sizing: border-box; margin: 0; padding: 0; }
  html, body {
    width: 1200px; height: 899px; overflow: hidden;
    background: var(--stage);
    font-family: "Exo 2", Arial, sans-serif;
  }
  .stage { position: relative; width: 1200px; height: 899px; }
  .card {
    position: absolute; left: 270px; width: 660px; height: 377px;
    background: var(--card-white);
    box-shadow: 0 6px 18px rgba(0,0,0,.18);
    overflow: hidden;
  }
  .card--back { top: 48px; }
  .card--front { top: 474px; }
  .card__shapes { position: absolute; inset: 0; width: 100%; height: 100%; }

  /* back side */
  .back__website {
    position: absolute; left: 30px; top: 152px;
    color: var(--ink-white); font-size: 15px; letter-spacing: .5px;
  }
  .back__brand-ghost {
    position: absolute; left: 360px; top: 140px;
    display: flex; align-items: center; gap: 14px;
    color: var(--ghost); font-size: 56px; font-weight: 600;
  }
  .back__brand-ghost .dot {
    width: 28px; height: 28px; border-radius: 50%; background: var(--ghost);
  }

  /* front side */
  .front__brand {
    position: absolute; left: 48px; top: 150px;
    display: flex; align-items: center; gap: 12px;
  }
  .front__brand .dot {
    width: 26px; height: 26px; border-radius: 50%; background: var(--accent-blue);
  }
  .front__brand .name {
    color: var(--ink-grey); font-size: 58px; font-weight: 600; letter-spacing: -.5px;
  }
  .front__details {
    position: absolute; right: 34px; top: 30px;
    text-align: right; color: var(--ink-white);
  }
  .person__name { font-size: 19px; font-weight: 500; letter-spacing: 1.5px; }
  .person__title { font-size: 14px; margin-top: 2px; }
  .address { font-size: 14px; line-height: 1.35; margin-top: 30px; }
  .contacts { list-style: none; margin-top: 26px; }
  .contacts li {
    display: flex; justify-content: flex-end; align-items: center; gap: 8px;
    font-size: 13px; line-height: 23px;
  }
  .contacts svg { width: 14px; height: 14px; fill: none; stroke: var(--ink-white); stroke-width: 1.6; }
</style>
</head>
<body>
<main class="stage">

  <section class="card card--back" aria-label="Card back">
    <svg class="card__shapes" viewBox="0 0 660 377" preserveAspectRatio="none" aria-hidden="true">
      <polygon points="0,0 180,0 262,165 200,377 0,377" fill="var(--card-grey)"/>
      <polygon points="180,0 200,0 282,160 200,377 262,165" fill="var(--accent-yellow)"/>
      <polygon points="196,377 262,165 268,168 204,377" fill="#4a4a4b"/>
    </svg>
    <p class="back__website">www.nimbora.net</p>
    <div class="back__brand-ghost" aria-hidden="true"><span class="dot"></span><span>Nimbora</span></div>
  </section>

  <section class="card card--front" aria-label="Card front">
    <svg class="card__shapes" viewBox="0 0 660 377" preserveAspectRatio="none" aria-hidden="true">
      <polygon points="222,0 660,0 660,377 282,377 352,170" fill="var(--card-grey)"/>
      <polygon points="200,0 222,0 360,166 338,172" fill="var(--accent-yellow)"/>
      <polygon points="338,172 360,166 292,377 282,377" fill="#4a4a4b"/>
    </svg>

    <div class="front__brand">
      <span class="dot"></span><span class="name">Nimbora</span>
    </div>

    <div class="front__details">
      <p class="person__name">MARCUS HALE</p>
      <p class="person__title">Managing Director</p>
      <p class="address">47 Harbour Lane, Level 9<br>Docklands VIC</p>
      <ul class="contacts">
        <li>03 9555 0147
          <svg viewBox="0 0 16 16"><path d="M3 2l3 0 1 3-2 1c1 2 3 4 5 5l1-2 3 1 0 3c-6 0-11-5-11-11z"/></svg></li>
        <li>0412 555 014
          <svg viewBox="0 0 16 16"><rect x="4" y="1" width="8" height="14" rx="1.5"/><line x1="7" y1="12.5" x2="9" y2="12.5"/></svg></li>
        <li>03 9555 0148
          <svg viewBox="0 0 16 16"><rect x="2" y="6" width="12" height="8" rx="1"/><rect x="4" y="2" width="8" height="4"/></svg></li>
        <li>hello@nimbora.net
          <svg viewBox="0 0 16 16"><rect x="1.5" y="3.5" width="13" height="9"/><polyline points="1.5,3.5 8,9 14.5,3.5"/></svg></li>
        <li>www.nimbora.net
          <svg viewBox="0 0 16 16"><circle cx="8" cy="8" r="6.5"/><ellipse cx="8" cy="8" rx="3" ry="6.5"/><line x1="1.5" y1="8" x2="14.5" y2="8"/></svg></li>
      </ul>
    </div>
  </section>

</main>
</body>
</html>
```